Business card for my new company (Accounting firm)

I need a business card for my new business Brightwell Advisory and Ledger SA. Our services are accounting, tax, audit and financial management. Our customers are small companies, start-ups and new companies. The final design has to show financial security, trust and growth. Please find our logo attached to the business card. Text for the business card: Brightwell Advisory and Ledger SA Tomas Varenholt Director and Founder Certified Accountant Tel. 022 418 57 34 tv@clairevalconseil.ch www.clairevalconseil.ch Rue des Vergières 27 1201 Geneva
Target Market(s)
Our customers are small companies, start-ups and new companies.
Industry/Entity Type
Finance And Accounting
Contact Information for Business Card
Claireval Conseil et Comptes SA
Tomas Varenholt
Directeur et Fondateur
Expert-comptable diplômé
Tél. 022 418 57 34
tv@clairevalconseil.ch
www.clairevalconseil.ch
Rue des Vergières 27
1201 Genève

```html
<!DOCTYPE html>
<html lang="en">
<head>
<meta charset="utf-8">
<title>Claireval Conseil et Comptes – Business Card</title>
<link rel="stylesheet" href="https://fonts.googleapis.com/css2?family=Lato:wght@400;700;900&display=swap">
<style>
  :root {
    --bg: #d9d9db;
    --card-white: #fbf7f7;
    --ink: #3a3a3c;
    --ink-soft: #6b6b6e;
    --blue-light: #2fb2e6;
    --blue-mid: #1e8fd0;
    --blue-dark: #1c6aa8;
    --rule: #c9c6c6;
  }
  * { box-sizing: border-box; margin: 0; padding: 0; }
  html, body { width: 1200px; height: 782px; overflow: hidden; }
  body {
    background: var(--bg);
    font-family: "Lato", Arial, sans-serif;
    color: var(--ink);
    position: relative;
  }
  .card {
    position: absolute;
    width: 530px;
    height: 306px;
    top: 238px;
    border-radius: 2px;
    box-shadow: 0 6px 18px rgba(0,0,0,.22);
    overflow: hidden;
  }
  /* Front */
  .card-front { left: 48px; background: var(--card-white); }
  .brand {
    position: absolute;
    left: 34px; top: 104px;
    width: 196px;
    display: flex; align-items: flex-start; gap: 10px;
  }
  .brand-mark {
    width: 18px; height: 18px; flex: none; margin-top: 5px;
    background: var(--blue-light);
  }
  .brand-name {
    font-weight: 900;
    font-size: 22px;
    line-height: 1.1;
    letter-spacing: .04em;
    text-transform: uppercase;
    color: var(--ink);
  }
  .divider {
    position: absolute;
    left: 250px; top: 48px;
    width: 1px; height: 170px;
    background: var(--rule);
  }
  .details { position: absolute; left: 274px; top: 58px; font-size: 15px; line-height: 1.3; }
  .person-name {
    color: var(--blue-light);
    font-weight: 900;
    font-size: 17px;
    text-transform: uppercase;
    letter-spacing: .01em;
  }
  .role { color: var(--ink); }
  .contact { list-style: none; margin-top: 2px; }
  .contact li { display: flex; align-items: center; gap: 6px; }
  .contact svg { width: 12px; height: 12px; flex: none; fill: var(--blue-mid); }
  .address { margin-top: 2px; }
  .band {
    position: absolute; left: 0; right: 0; bottom: 0; height: 22px;
    display: flex;
  }
  .band span:nth-child(1) { flex: 34; background: var(--blue-dark); }
  .band span:nth-child(2) { flex: 40; background: var(--blue-light); }
  .band span:nth-child(3) { flex: 26; background: var(--blue-mid); }

  /* Back */
  .card-back {
    left: 622px;
    background: linear-gradient(160deg, var(--blue-dark) 0%, var(--blue-light) 48%, var(--blue-mid) 100%);
  }
  .back-pattern {
    position: absolute; inset: 0;
    background: linear-gradient(160deg, rgba(255,255,255,.05), rgba(255,255,255,.12) 50%, rgba(255,255,255,.04));
  }
  .back-brand {
    position: absolute; left: 0; right: 0; top: 200px;
    text-align: center;
    color: #fff;
    font-weight: 900;
    font-size: 18px;
    letter-spacing: .08em;
    text-transform: uppercase;
  }
</style>
</head>
<body>
  <section class="card card-front" aria-label="Business card front">
    <div class="brand">
      <span class="brand-mark"></span>
      <span class="brand-name">Claireval Conseil et Comptes</span>
    </div>
    <div class="divider"></div>
    <div class="details">
      <p class="person-name">SA Tomas Varenholt</p>
      <p class="role">Director and Founder</p>
      <p class="role">Certified Accountant</p>
      <ul class="contact">
        <li><svg viewBox="0 0 24 24"><path d="M6.6 10.8a15 15 0 0 0 6.6 6.6l2.2-2.2a1 1 0 0 1 1-.25 11.4 11.4 0 0 0 3.6.57 1 1 0 0 1 1 1V20a1 1 0 0 1-1 1A17 17 0 0 1 3 4a1 1 0 0 1 1-1h3.5a1 1 0 0 1 1 1c0 1.25.2 2.45.57 3.57a1 1 0 0 1-.25 1z"/></svg>022 418 57 34</li>
        <li><svg viewBox="0 0 24 24"><path d="M2 5h20v14H2zm2 2v.4l8 5 8-5V7zm0 2.8V17h16V9.8l-8 5z"/></svg>tv@clairevalconseil.ch</li>
        <li><svg viewBox="0 0 24 24"><circle cx="12" cy="12" r="10"/></svg>www.clairevalconseil.ch</li>
      </ul>
      <p class="address">Rue des Vergières 27<br>1201 Geneva</p>
    </div>
    <div class="band"><span></span><span></span><span></span></div>
  </section>

  <section class="card card-back" aria-label="Business card back">
    <div class="back-pattern" role="img" aria-label="Repeating brand pattern in light blue tones"></div>
    <p class="back-brand">Claireval</p>
  </section>
</body>
</html>
```